KRT Engineering Business Card Design

We’re looking for an elegant, clean, and timeless business card design that communicates experience, capability, and reliability.

KRT Engineering was established in 1995 , we are a Government Contracting company providing Professional Services to the Office of Frontier Affairs, Harbor Protection and the Vantage Collective. Our capabilities include: Acquisition & Program Management; Intelligence & Security Operations; Cyber, IT & Network Operations; Lifecycle Logistics & Asset Readiness; C5ISR Systems Engineering & Sustainment.

We want the card to reflect a straightforward, confident approach to business. The design should feel polished and professional without being flashy or overly corporate.

Design Direction
Clean, sophisticated, and uncluttered
Elegant but understated
Strong typography and thoughtful spacing
A timeless aesthetic rather than something overly trendy
Confident and established, with a sense of substance
Easy to read and practical in a real-world business setting

The overall impression should be: “These are experienced professionals who know what they’re doing, do what they say, and can be relied upon.”

We’re open to creative interpretations. The finished card should feel distinctive through its typography, proportions, layout, and attention to detail rather than through excessive graphics or visual effects.

We’re looking for a design that would make a potential client immediately feel that they’re dealing with a capable, trustworthy, and established company.

Company Colors: Navy and Gold/Yellow (but you do not need to use these colors on the card)
Company Name: KRT Engineering Associates, Inc. (known as KRT Engineering)
Website: krtengineering.com
Company Logo: Navy & Gold (other variations attached)

```html
<!DOCTYPE html>
<html lang="en">
<head>
<meta charset="utf-8">
<title>KRT Engineering Business Card</title>
<link rel="stylesheet" href="https://fonts.googleapis.com/css2?family=Arimo:wght@700&family=Poppins:wght@400;500&display=swap">
<style>
  :root {
    --navy: #232a5c;
    --navy-light: #2f3570;
    --gold: #fde24f;
    --white: #ffffff;
    --backdrop: #6e6e70;
  }
  * { margin: 0; padding: 0; box-sizing: border-box; }
  html, body {
    width: 900px; height: 1200px; overflow: hidden;
    background: var(--backdrop);
  }
  .canvas { position: relative; width: 900px; height: 1200px; }

  .card {
    position: absolute;
    left: 136px;
    width: 630px;
    height: 363px;
    overflow: hidden;
  }

  /* Front */
  .card-front {
    top: 214px;
    background: linear-gradient(100deg, var(--navy) 0%, var(--navy-light) 100%);
    display: flex; align-items: center; justify-content: center;
  }
  .front-wordmark {
    font-family: "Arimo", Arial, sans-serif;
    font-weight: 700;
    font-size: 48px;
    color: var(--white);
    letter-spacing: 0.5px;
  }

  /* Back */
  .card-back {
    top: 629px;
    background: var(--white);
    color: var(--navy);
    font-family: "Poppins", Arial, sans-serif;
  }
  .person { position: absolute; left: 42px; top: 50px; }
  .person-name {
    font-family: "Arimo", Arial, sans-serif;
    font-weight: 700;
    font-size: 24px;
    line-height: 1;
  }
  .person-title {
    margin-top: 8px;
    margin-left: 1px;
    font-size: 17px;
    line-height: 1;
  }
  .divider {
    position: absolute; left: 43px; width: 148px; height: 1.5px;
    background: var(--navy);
  }
  .divider-top { top: 115px; }
  .divider-bottom { top: 207px; }
  .address {
    position: absolute; left: 43px; top: 124px;
    font-size: 17px; line-height: 25px; font-style: normal;
  }
  .contacts { position: absolute; left: 43px; top: 224px; list-style: none; }
  .contact {
    display: flex; align-items: center; gap: 6px;
    font-size: 17.5px; line-height: 1; height: 28px;
    letter-spacing: 0.3px;
  }
  .contact svg { width: 18px; height: 18px; flex: none; }

  .back-wordmark {
    position: absolute; right: 44px; top: 172px;
    font-family: "Arimo", Arial, sans-serif;
    font-weight: 700;
    font-size: 36px;
    color: var(--navy);
  }

  .footer-band { position: absolute; left: 0; bottom: 0; width: 630px; height: 20px; }
</style>
</head>
<body>
<main class="canvas">

  <section class="card card-front" aria-label="Card front">
    <span class="front-wordmark">KRT Engineering</span>
  </section>

  <section class="card card-back" aria-label="Card back">
    <div class="person">
      <h1 class="person-name">Marion Keller, P.E.</h1>
      <p class="person-title">CEO &amp; President</p>
    </div>

    <div class="divider divider-top"></div>
    <address class="address">
      4820 Harbor Point Road,<br>
      Suite 310, Norfolk,<br>
      VA 23510
    </address>
    <div class="divider divider-bottom"></div>

    <ul class="contacts">
      <li class="contact">
        <svg viewBox="0 0 20 20" aria-hidden="true">
          <circle cx="10" cy="10" r="10" fill="var(--navy)"/>
          <path d="M6.3 5.2l1.9-.4 1.1 2.6-1.3 1c.6 1.3 1.6 2.3 2.9 2.9l1-1.3 2.6 1.1-.4 1.9c-4.2.3-8.1-3.6-7.8-7.8z" fill="var(--gold)"/>
        </svg>
        757-555-0142
      </li>
      <li class="contact">
        <svg viewBox="0 0 20 20" aria-hidden="true">
          <circle cx="10" cy="10" r="10" fill="var(--gold)"/>
          <g fill="none" stroke="var(--navy)" stroke-width="1.2">
            <circle cx="10" cy="10" r="6"/>
            <ellipse cx="10" cy="10" rx="2.6" ry="6"/>
            <line x1="4" y1="10" x2="16" y2="10"/>
            <line x1="5" y1="7" x2="15" y2="7"/>
            <line x1="5" y1="13" x2="15" y2="13"/>
          </g>
        </svg>
        krtengineering.com
      </li>
      <li class="contact">
        <svg viewBox="0 0 20 20" aria-hidden="true">
          <circle cx="10" cy="10" r="10" fill="var(--gold)"/>
        </svg>
        krt-engineering-associates-inc
      </li>
    </ul>

    <span class="back-wordmark">KRT Engineering</span>

    <svg class="footer-band" viewBox="0 0 630 20" preserveAspectRatio="none" aria-hidden="true">
      <polygon points="0,0 529,0 517,20 0,20" fill="var(--navy)"/>
      <polygon points="538,0 630,0 630,20 526,20" fill="var(--gold)"/>
    </svg>
  </section>

</main>
</body>
</html>
```